Animal Horse & Bedding Company Needs a Website Coded & Designed

We need a website for a new animal bedding and feed company that is visually grabbing and vibrant. We would like to see a website that displays trust, quality and confidence. Needs to be responsive and mobile friendly for all browsers and coded for both Android & IOS. SEO is also important.

Joomla or Wordpress – must be both desktop and mobile friendly with fast page load speed. Need the ability to edit ourselves in Wordpress or Joomla.

Full details attached below with some layout and content ideas.

Coding

Coded - Design and coding required

Number of Pages Required

5+ page

Font styles to use
Sans Serif

Requirements
Must have
• Needs to be responsive and mobile friendly for all browsers and coded for both Android & IOS. SEO is also important.

Wordpress – must be both desktop and mobile friendly with fast page load speed. Need the ability to edit ourselves in Wordpress.

Logo Colours:
Dark Brown
CMYK: 50 / 70 / 80 / 70
Pantone: 4625C

Orange
CMYK: 0 / 50 / 100 / 0
Pantone: 144C
Nice to have
• Use picture of building attached and super impose logo on building.

```html
<!DOCTYPE html>
<html lang="en">
<head>
<meta charset="utf-8">
<title>Hay Harbor – Website Pages</title>
<link href="https://fonts.googleapis.com/css2?family=Oswald:wght@300;400&family=Montserrat:wght@400;600;700&display=swap" rel="stylesheet">
<style>
:root{
  --board:#b2b2b2;
  --brown:#3c2415;
  --orange:#f7941d;
  --beige:#faf6f0;
  --blush:#fcf1ef;
  --ink:#4a3b33;
  --muted:#6d625b;
  --white:#ffffff;
  --line:#d9d2cc;
}
*{box-sizing:border-box;margin:0;padding:0}
html,body{width:1200px;height:1200px;overflow:hidden;background:var(--board)}
body{position:relative;font-family:"Montserrat",sans-serif;color:var(--ink)}
.page{position:absolute;width:365px;background:var(--white);overflow:hidden}
.page > *{position:absolute}
.page-about{left:36px;top:40px;height:556px}
.page-feed{left:36px;top:614px;height:500px}
.page-bedding{left:424px;top:40px;height:890px}
.page-quote{left:804px;top:40px;height:496px}

/* header */
.site-header{left:0;top:0;width:365px;height:29px;background:var(--white);z-index:2}
.brand{position:absolute;left:22px;top:10px;font-family:"Montserrat",sans-serif;font-weight:600;font-size:8px;line-height:9px;color:var(--brown)}
.main-nav{position:absolute;left:130px;top:11px;display:flex;gap:16px;font-size:4px;color:var(--ink);text-transform:uppercase}
.main-nav .active{font-weight:700;color:var(--brown);border-bottom:1px solid var(--orange);padding-bottom:3px}
.quote-pill{position:absolute;left:298px;top:8px;width:47px;height:12px;border-radius:6px;background:var(--brown);color:var(--white);font-size:3.3px;font-weight:700;display:flex;align-items:center;justify-content:center}

/* hero */
.hero{left:0;top:29px;width:365px;height:156px}
.hero svg{display:block}
.hero-title{position:absolute;left:0;width:365px;text-align:center;font-family:"Oswald",sans-serif;font-weight:400;color:var(--white);letter-spacing:1px}

/* shared type */
.h2{font-family:"Oswald",sans-serif;font-weight:300;color:var(--brown);letter-spacing:.5px}
.rule{display:block;width:16px;height:1px;background:var(--orange);margin-top:4px}
.copy{font-size:3.4px;line-height:8.2px;color:var(--muted)}
.btn{display:flex;align-items:center;justify-content:center;background:var(--orange);color:var(--white);font-weight:700;border-radius:3px 10px 3px 3px;text-transform:uppercase}

/* footer */
.site-footer{left:0;bottom:0;width:365px;height:149px;background:var(--brown);color:var(--white)}
.site-footer > *{position:absolute}
.footer-curve{left:0;top:0}
.footer-brand{left:34px;top:66px;width:82px;text-align:center;font-family:"Montserrat",sans-serif;font-weight:600;font-size:9px;line-height:10px;color:var(--white)}
.footer-col h4{font-size:3.8px;font-weight:600;letter-spacing:.2px;margin-bottom:5px}
.footer-col li{list-style:none;font-size:3px;line-height:8px;color:#e7ddd6}
.col-sitemap{left:132px;top:52px}
.col-contact{left:185px;top:52px}
.col-contact li{display:flex;gap:3px;align-items:center}
.col-contact i{width:3px;height:3px;border-radius:50%;background:var(--orange);display:inline-block}
.col-news{left:266px;top:52px}
.news-field{width:70px;height:11px;border:1px solid #8c7566;border-radius:6px;font-size:3px;color:#d8ccc4;padding:3px 6px}
.news-btn{margin:3px 0 0 2px;width:40px;height:10px;border-radius:5px;background:var(--white);color:var(--brown);font-size:3px;font-weight:700;display:flex;align-items:center;justify-content:center}
.footer-rule{left:0;top:127px;width:365px;height:1px;background:#52372a}
.copyright{left:0;top:135px;width:365px;text-align:center;font-size:2.8px;color:#bfb1a7}

/* about */
.feature-band{left:0;top:350px;width:365px;height:90px;background:var(--beige)}
.feature{top:377px;width:100px;display:flex;gap:5px}
.feature .ico{flex:none;width:15px;height:15px;border:1.2px solid var(--orange);border-radius:50%}
.feature h5{font-size:4.6px;line-height:5.5px;font-weight:400;color:var(--brown);text-transform:uppercase}
.feature p{font-size:2.8px;line-height:5.5px;color:var(--muted);margin-top:2px}

/* bedding */
.benefit-band{left:0;top:353px;width:365px;height:234px;background:var(--blush)}
.benefit-dot{width:22px;height:22px;border-radius:50%;background:var(--orange);display:flex;align-items:center;justify-content:center}
.benefit-dot.dark{background:var(--brown)}
.benefit-dot::after{content:"";width:9px;height:9px;border:1px solid var(--white);border-radius:50%}
.benefit-label{font-size:4px;line-height:5.5px;color:var(--brown)}
.service-card{top:619px;width:95px;height:111px;border:1px solid var(--line);text-align:center;padding-top:10px}
.service-card .ico{width:11px;height:13px;border:1px solid var(--orange);border-radius:2px;margin:0 auto 6px}
.service-card h5{font-family:"Oswald",sans-serif;font-weight:400;font-size:6px;color:var(--brown);letter-spacing:.3px}
.service-card p{font-size:3px;line-height:5.8px;color:var(--ink);margin:4px 6px 0}
.service-card .btn{width:50px;height:11px;font-size:3.2px;margin:6px auto 0}

/* quote */
.field{border:1px solid #c9c0b8;font-size:3.2px;color:var(--muted);padding:4px 6px;background:var(--white)}

/* feed */
.feed-perk{display:flex;align-items:center;gap:3px;font-size:2.6px;font-weight:700;line-height:3.4px;color:var(--brown);width:48px}
.feed-perk i{flex:none;width:9px;height:9px;border:1px solid var(--orange);border-radius:50%}
</style>
</head>
<body>

<!-- ABOUT PAGE -->
<section class="page page-about">
  <header class="site-header">
    <div class="brand">Hay Harbor</div>
    <nav class="main-nav"><span class="active">Home</span><span>About</span><span>Feed</span><span>Bedding</span><span>Contact Us</span></nav>
    <span class="quote-pill">REQUEST QUOTE ›</span>
  </header>
  <div class="hero">
    <svg width="365" height="156" viewBox="0 0 365 156" role="img" aria-label="Chestnut horse galloping through a meadow of purple wildflowers">
      <defs><linearGradient id="heroAbout" x1="0" y1="0" x2="0" y2="1">
        <stop offset="0" stop-color="#a9b2b4"/><stop offset=".4" stop-color="#6f7e63"/><stop offset=".75" stop-color="#8a6e7a"/><stop offset="1" stop-color="#6b7c4a"/></linearGradient>
        <radialGradient id="heroAboutHorse" cx=".5" cy=".55" r=".25"><stop offset="0" stop-color="#8a4a24" stop-opacity=".9"/><stop offset="1" stop-color="#8a4a24" stop-opacity="0"/></radialGradient></defs>
      <rect width="365" height="156" fill="url(#heroAbout)"/>
      <rect width="365" height="156" fill="url(#heroAboutHorse)"/>
      <path d="M0 118 Q182 176 365 118 L365 156 L0 156 Z" fill="#fff"/>
      <path d="M0 123 Q182 180 365 123" fill="none" stroke="#f7941d" stroke-width="1.6"/>
    </svg>
    <div class="hero-title" style="top:52px;font-size:28px">ABOUT</div>
  </div>

  <div role="img" aria-label="Portrait of a chestnut horse in a green field" style="left:41px;top:202px;width:126px;height:126px;border-radius:50%;background:radial-gradient(circle at 55% 55%,#9c5a2c 0,#a86a3a 25%,#86a0a8 55%,#7f9a5e 100%)"></div>
  <div style="left:182px;top:216px;width:160px">
    <div class="h2" style="font-size:13px">ABOUT US</div><span class="rule"></span>
    <p class="copy" style="margin-top:12px">Hay Harbor is a locally owned company located in Pinecrest, AB. We are dedicated in providing high quality products and services. Producing, buying and marketing hay and straw for x amount of years. Insert blurb on ownership/history of key staff/owners.</p>
  </div>
  <div class="btn" style="left:183px;top:289px;width:67px;height:16px;font-size:4.4px">REQUEST QUOTE ›</div>

  <div class="feature-band"></div>
  <div class="feature" style="left:33px"><span class="ico"></span><div><h5>Quality<br>Guaranteed</h5><p>Grown for quality - 100% natural with no chemicals or additives</p></div></div>
  <div class="feature" style="left:140px"><span class="ico"></span><div><h5>Full Service<br>Solution</h5><p>Dedicated in providing a full service solution of bedding supply &amp; waste removal</p></div></div>
  <div class="feature" style="left:250px"><span class="ico"></span><div><h5>Convenient &amp; Cost<br>Effective</h5><p>Compressed bags , pellets or bulk products saving in shipping costs</p></div></div>

  <footer class="site-footer">
    <svg class="footer-curve" width="365" height="34" viewBox="0 0 365 34"><path d="M0 0 Q182 62 365 0 L365 -1 L0 -1 Z" fill="#faf6f0"/></svg>
    <div class="footer-brand">Hay Harbor</div>
    <div class="footer-col col-sitemap"><h4>SITEMAP</h4><ul><li>Home</li><li>About Us</li><li>Our Bedding</li><li>Feed</li><li>Contact Us</li></ul></div>
    <div class="footer-col col-contact"><h4>CONTACT US</h4><ul><li><i></i>123 Avenue name, City name</li><li>&nbsp;&nbsp;&nbsp;25252, United States</li><li><i></i>(555) 014-2290</li><li><i></i>hello@hayharbor.com</li></ul></div>
    <div class="footer-col col-news"><h4>NEWSLETTER SIGN UP</h4><div class="news-field">Email address</div><div class="news-btn">SUBSCRIBE</div></div>
    <span class="footer-rule"></span>
    <p class="copyright">© Copyright 2020 . Hay Harbor . All Right Reserved</p>
  </footer>
</section>

<!-- FEED PAGE -->
<section class="page page-feed">
  <header class="site-header">
    <div class="brand">Hay Harbor</div>
    <nav class="main-nav"><span>Home</span><span>About</span><span class="active">Feed</span><span>Bedding</span><span>Contact Us</span></nav>
    <span class="quote-pill">REQUEST QUOTE ›</span>
  </header>
  <div class="hero">
    <svg width="365" height="156" viewBox="0 0 365 156" role="img" aria-label="Woman resting her head against a brown and white horse among yellow flowers">
      <defs><linearGradient id="heroFeed" x1="0" y1="0" x2="1" y2="0">
        <stop offset="0" stop-color="#6a3518"/><stop offset=".3" stop-color="#a96a3c"/><stop offset=".5" stop-color="#9aa33a"/><stop offset=".75" stop-color="#b98d62"/><stop offset="1" stop-color="#c9b23a"/></linearGradient></defs>
      <rect width="365" height="156" fill="url(#heroFeed)"/>
      <path d="M0 118 Q182 176 365 118 L365 156 L0 156 Z" fill="#fff"/>
      <path d="M0 123 Q182 180 365 123" fill="none" stroke="#f7941d" stroke-width="1.6"/>
    </svg>
    <div class="hero-title" style="top:47px;font-size:26px">FEED</div>
  </div>

  <div role="img" aria-label="Man feeding a horse from a bucket at a stable fence" style="left:37px;top:206px;width:120px;height:131px;background:linear-gradient(135deg,#8e9aa0 0%,#6e4a32 40%,#b3a89a 65%,#7a6a5c 100%)"></div>
  <div style="left:174px;top:211px;width:158px">
    <div class="h2" style="font-size:13px">OUR FEED</div><span class="rule"></span>
    <p class="copy" style="margin-top:9px">Hay cubes and pellets are made from premium hay offering a variety of animals a feed that is non-GMO and packed with natural nutrients. These pellets and cubes are less bulky to handle, store and ship. As well, they reduce the amount of wasted feed.</p>
  </div>
  <div class="feed-perk" style="left:175px;top:280px"><i></i>100% Natural</div>
  <div class="feed-perk" style="left:229px;top:280px"><i></i>Chemical &amp; Additive Free</div>
  <div class="feed-perk" style="left:283px;top:280px"><i></i>Available in Pellets or Cubes</div>
  <div class="feed-perk" style="left:175px;top:302px"><i></i>Clean - Eliminates Dust From Feeding Baled Hay</div>
  <div class="feed-perk" style="left:229px;top:302px"><i></i>Eliminate Waste In Feeding</div>
  <div class="feed-perk" style="left:283px;top:302px"><i></i>High Protein Content</div>
  <div class="feed-perk" style="left:175px;top:324px"><i></i>Cost Effective</div>
  <div class="feed-perk" style="left:229px;top:324px"><i></i>Convenient</div>
  <div class="feed-perk" style="left:283px;top:324px"><i></i>Less wasted feed</div>

  <footer class="site-footer">
    <svg class="footer-curve" width="365" height="34" viewBox="0 0 365 34"><path d="M0 0 Q182 62 365 0 L365 -1 L0 -1 Z" fill="#fff"/></svg>
    <div class="footer-brand">Hay Harbor</div>
    <div class="footer-col col-sitemap"><h4>SITEMAP</h4><ul><li>Home</li><li>About Us</li><li>Our Bedding</li><li>Feed</li><li>Contact Us</li></ul></div>
    <div class="footer-col col-contact"><h4>CONTACT US</h4><ul><li><i></i>123 Avenue name, City name</li><li>&nbsp;&nbsp;&nbsp;25252, United States</li><li><i></i>(555) 014-2290</li><li><i></i>hello@hayharbor.com</li></ul></div>
    <div class="footer-col col-news"><h4>NEWSLETTER SIGN UP</h4><div class="news-field">Email address</div><div class="news-btn">SUBSCRIBE</div></div>
    <span class="footer-rule"></span>
    <p class="copyright">© Copyright 2020 . Hay Harbor . All Right Reserved</p>
  </footer>
</section>

<!-- BEDDING PAGE -->
<section class="page page-bedding">
  <header class="site-header">
    <div class="brand">Hay Harbor</div>
    <nav class="main-nav"><span>Home</span><span>About</span><span>Feed</span><span class="active">Bedding</span><span>Contact Us</span></nav>
    <span class="quote-pill">REQUEST QUOTE ›</span>
  </header>
  <div class="hero">
    <svg width="365" height="156" viewBox="0 0 365 156" role="img" aria-label="Young foal lying down in straw bedding">
      <defs><linearGradient id="heroBedding" x1="0" y1="0" x2="1" y2="1">
        <stop offset="0" stop-color="#7a4a2a"/><stop offset=".45" stop-color="#c08a5a"/><stop offset=".7" stop-color="#9c6a44"/><stop offset="1" stop-color="#b78a62"/></linearGradient></defs>
      <rect width="365" height="156" fill="url(#heroBedding)"/>
      <path d="M0 118 Q182 176 365 118 L365 156 L0 156 Z" fill="#fff"/>
      <path d="M0 123 Q182 180 365 123" fill="none" stroke="#f7941d" stroke-width="1.6"/>
    </svg>
    <div class="hero-title" style="top:45px;font-size:26px">BEDDING</div>
  </div>

  <div style="left:42px;top:213px;width:152px">
    <div class="h2" style="font-size:12px">BEDDING</div><span class="rule"></span>
    <p class="copy" style="margin-top:9px">Clean, dry, natural solution<br>For many people, their animals, whether it be a horse, goat or other are more than just an animal, they are a part of your family, a way of life, and their comfort is important. Fine cut 100% chopped straw offers a softer bedding for your equine or other large and/or small animal.</p>
    <p class="copy" style="margin-top:8px">This straw bedding is light weight which allows for easier spreading, re-moving and hauling away. Straw also decomposes a lot faster than wood shavings and makes for great compost material.</p>
  </div>
  <div role="img" aria-label="Close-up of fine chopped straw bedding" style="left:209px;top:211px;width:121px;height:112px;background:radial-gradient(circle at 30% 40%,#f3e2c4 0,#d9b98a 45%,#c49a66 100%)"></div>

  <div class="benefit-band"></div>
  <div class="h2" style="left:0;top:373px;width:365px;text-align:center;font-size:12px">BENEFITS</div>
  <span style="left:174px;top:391px;width:16px;height:1px;background:var(--orange)"></span>
  <svg style="left:0;top:400px" width="365" height="180" viewBox="0 0 365 180" fill="none" stroke="#9a918b" stroke-width=".6">
    <path d="M111 22 Q122 18 128 28"/><path d="M239 22 Q228 18 222 28"/>
    <path d="M108 80 Q114 88 124 86"/><path d="M242 80 Q236 88 226 86"/>
    <path d="M129 118 Q140 114 142 106"/><path d="M221 118 Q210 114 208 106"/>
    <path d="M175 112 L175 128"/>
  </svg>
  <div role="img" aria-label="Chestnut horse portrait" style="left:123px;top:404px;width:106px;height:106px;border-radius:50%;background:radial-gradient(circle at 55% 50%,#9c5a2c 0,#a86a3a 28%,#8fa6ae 58%,#7f9a5e 100%)"></div>
  <div class="benefit-dot" style="left:81px;top:411px"></div>
  <div class="benefit-label" style="left:34px;top:412px;width:44px;text-align:right">100% Natural Chopped Straw</div>
  <div class="benefit-dot" style="left:247px;top:411px"></div>
  <div class="benefit-label" style="left:274px;top:412px;width:70px">Environmentally Friendly – Recyclable &amp; Compostable</div>
  <div class="benefit-dot dark" style="left:86px;top:463px"></div>
  <div class="benefit-label" style="left:52px;top:467px;width:31px;text-align:right">Low Dust</div>
  <div class="benefit-dot dark" style="left:240px;top:463px"></div>
  <div class="benefit-label" style="left:266px;top:464px;width:60px">Economic – less used and less wasted</div>
  <div class="benefit-dot" style="left:106px;top:512px"></div>
  <div class="benefit-label" style="left:65px;top:513px;width:38px;text-align:right">Chemical &amp; Additive Free</div>
  <div class="benefit-dot" style="left:220px;top:512px"></div>
  <div class="benefit-label" style="left:246px;top:513px;width:50px">Cheaper than Wood Shavings</div>
  <div class="benefit-dot dark" style="left:164px;top:536px"></div>

  <div class="service-card" style="left:37px"><div class="ico"></div><h5>AVAILABLE BY THE BAG</h5><p>Bagged for easy storage</p><div class="btn">REQUEST QUOTE ›</div></div>
  <div class="service-card" style="left:136px"><div class="ico"></div><h5>BULK DELIVERY</h5><p style="font-size:3.3px">Let Us Deliver To You</p><p style="font-size:2.6px;line-height:5.8px;margin-top:1px">Bulk alternative to bagged bedding. Bulk materials are more economical, arrive loose, in a trailer so there is no plastic waste. This is a cheaper solution to bagged shavings.<br>Bulk pricing and delivery</p><div class="btn" style="margin-top:4px">REQUEST QUOTE ›</div></div>
  <div class="service-card" style="left:235px"><div class="ico"></div><h5>REMOVAL OF WASTE</h5><p style="font-size:2.6px">Let us remove your waste bedding. Need to insert blurb on service. Insert service of back hauling away manure</p><div class="btn">REQUEST QUOTE ›</div></div>

  <footer class="site-footer">
    <svg class="footer-curve" width="365" height="34" viewBox="0 0 365 34"><path d="M0 0 Q182 62 365 0 L365 -1 L0 -1 Z" fill="#fff"/></svg>
    <div class="footer-brand">Hay Harbor</div>
    <div class="footer-col col-sitemap"><h4>SITEMAP</h4><ul><li>Home</li><li>About Us</li><li>Our Bedding</li><li>Feed</li><li>Contact Us</li></ul></div>
    <div class="footer-col col-contact"><h4>CONTACT US</h4><ul><li><i></i>123 Avenue name, City name</li><li>&nbsp;&nbsp;&nbsp;25252, United States</li><li><i></i>(555) 014-2290</li><li><i></i>hello@hayharbor.com</li></ul></div>
    <div class="footer-col col-news"><h4>NEWSLETTER SIGN UP</h4><div class="news-field">Email address</div><div class="news-btn">SUBSCRIBE</div></div>
    <span class="footer-rule"></span>
    <p class="copyright">© Copyright 2020 . Hay Harbor . All Right Reserved</p>
  </footer>
</section>

<!-- REQUEST QUOTE PAGE -->
<section class="page page-quote">
  <header class="site-header">
    <div class="brand">Hay Harbor</div>
    <nav class="main-nav"><span>Home</span><span>About</span><span>Feed</span><span>Bedding</span><span>Contact Us</span></nav>
    <span class="quote-pill">REQUEST QUOTE ›</span>
  </header>
  <div class="hero">
    <svg width="365" height="156" viewBox="0 0 365 156" role="img" aria-label="Three horses galloping together across a green pasture">
      <defs><linearGradient id="heroQuote" x1="0" y1="0" x2="1" y2="0">
        <stop offset="0" stop-color="#7c8e4a"/><stop offset=".3" stop-color="#3a2418"/><stop offset=".55" stop-color="#a8602e"/><stop offset=".8" stop-color="#8a4a24"/><stop offset="1" stop-color="#7f9a4a"/></linearGradient></defs>
      <rect width="365" height="156" fill="url(#heroQuote)"/>
      <path d="M0 118 Q182 176 365 118 L365 156 L0 156 Z" fill="#fff"/>
      <path d="M0 123 Q182 180 365 123" fill="none" stroke="#f7941d" stroke-width="1.6"/>
    </svg>
    <div class="hero-title" style="top:54px;font-size:17px">REQUEST QUOTE</div>
  </div>

  <div class="h2" style="left:0;top:203px;width:365px;text-align:center;font-size:13px">FILL OUR CONTACT FORM</div>
  <span style="left:174px;top:222px;width:16px;height:1px;background:var(--orange)"></span>
  <p class="copy" style="left:60px;top:229px;width:245px;text-align:center;line-height:7px">Praesent vitae lacus Ut velit enim vestibulum non fermentum nec hendrerit quis leo Pellentesque rutrum male-suada neque Nunc tempus felis vitae urna Vivamus porttitor neque at volutpat rutrum</p>
  <div class="field" style="left:70px;top:255px;width:111px;height:14px">First Name</div>
  <div class="field" style="left:185px;top:255px;width:111px;height:14px">Last Name</div>
  <div class="field" style="left:70px;top:274px;width:111px;height:14px">Email address</div>
  <div class="field" style="left:185px;top:274px;width:111px;height:14px">Phone</div>
  <div class="field" style="left:70px;top:293px;width:226px;height:29px">Message</div>
  <div class="btn" style="left:151px;top:332px;width:66px;height:17px;font-size:4.4px">SEND MESSAGE ›</div>

  <footer class="site-footer" style="height:146px">
    <svg class="footer-curve" width="365" height="34" viewBox="0 0 365 34"><path d="M0 0 Q182 62 365 0 L365 -1 L0 -1 Z" fill="#fff"/></svg>
    <div class="footer-brand">Hay Harbor</div>
    <div class="footer-col col-sitemap"><h4>SITEMAP</h4><ul><li>Home</li><li>About Us</li><li>Our Bedding</li><li>Feed</li><li>Contact Us</li></ul></div>
    <div class="footer-col col-contact"><h4>CONTACT US</h4><ul><li><i></i>123 Avenue name, City name</li><li>&nbsp;&nbsp;&nbsp;25252, United States</li><li><i></i>(555) 014-2290</li><li><i></i>hello@hayharbor.com</li></ul></div>
    <div class="footer-col col-news"><h4>NEWSLETTER SIGN UP</h4><div class="news-field">Email address</div><div class="news-btn">SUBSCRIBE</div></div>
    <p class="copyright" style="top:133px">© Copyright 2020 . Hay Harbor . All Right Reserved</p>
  </footer>
</section>

</body>
</html>
```